Corvana Tongue Works, LLC

We need a business card that includes information about our business and conveys a reliable business that provides document translation services and interpreters for a variety of corporate and individual clients. We want to come across as professional, reliable, yet approachable. It should include the following on one side:

ESL / ENL Language Classes, Private Lessons, and Online Tutors
PLEXA Training and Testing
Translating & Interpreting Services
Contact us about Over-the-Phone Interpreting in over 200 languages
24/7/365
www.corvanatongue.example

The other side should include (555) 481-3062

Rhoda Pelling, President
482 Garnet Ave., Ste. 219
Indianapolis, IN 40917

Please add USA as part of the address. Also, please add rmpelling@corvanatongueworks.example as the e-mail address. Thank you.

Target Market(s)

Business professionals, their families, the international community

Industry/Entity Type

Business

Contact Information for Business Card

24/7/365
www.corvanatongue.example

(555) 481-3062

Rhoda Pelling, President
482 Garnet Ave., Ste. 219
Indianapolis, IN 40917
USA

Font styles to use
Sans Serif

Colors

Designer to choose colors to be used in the design.

Requirements
Must have
• See project description
• e-mail address and web address
• Phone number
Nice to have
• a globe
• physical address
Should not have
• Should not have the same color scheme as other agencies in our market in Indiana unless it is blue and black. No purple or yellow.

```html
<!DOCTYPE html>
<html lang="en">
<head>
<meta charset="utf-8">
<title>Corvana Tongue Works – Business Card</title>
<link rel="stylesheet" href="https://fonts.googleapis.com/css2?family=Lato:wght@400;700;900&display=swap">
<style>
  :root {
    --brand-blue: #2a97d6;
    --ink: #141414;
    --card-white: #fbfbfb;
    --backdrop: #e6e6e6;
    --map-grey: #dcdcdc;
  }
  * { margin: 0; padding: 0; box-sizing: border-box; }
  html, body { width: 1200px; height: 960px; overflow: hidden; }
  body {
    position: relative;
    background: var(--backdrop);
    font-family: "Lato", sans-serif;
    color: var(--ink);
  }
  .card {
    position: absolute;
    width: 600px;
    height: 341px;
    background: var(--card-white);
    border-radius: 18px;
    overflow: hidden;
    box-shadow: 0 3px 6px rgba(0,0,0,0.25);
  }
  .card-front { left: 302px; top: 130px; }
  .card-back { left: 299px; top: 488px; }
  .card svg.shapes { position: absolute; inset: 0; }

  /* Front: brand name */
  .brand-mark {
    position: absolute; left: 50px; top: 58px;
    width: 92px; height: 92px; border-radius: 50%;
    background: var(--brand-blue);
    border: 3px solid var(--card-white);
    box-shadow: 0 0 0 2px var(--brand-blue);
  }
  .brand-name {
    position: absolute; left: 150px; top: 62px;
    font-size: 24px; font-weight: 400; line-height: 28px;
    color: var(--ink);
  }

  /* Front: contact block */
  .person {
    position: absolute; right: 43px; top: 144px; text-align: right;
  }
  .person-name { font-size: 21px; font-weight: 900; letter-spacing: 0.2px; }
  .person-title { font-size: 15px; font-weight: 900; margin-top: 1px; }
  .contact-list {
    position: absolute; right: 43px; top: 201px; text-align: right;
    font-size: 14px; line-height: 19px; list-style: none;
  }
  .contact-list li { display: flex; justify-content: flex-end; align-items: center; gap: 8px; }
  .contact-list .gap { margin-top: 12px; }
  .contact-list svg { width: 13px; height: 13px; flex: none; }
  .contact-list .spacer { width: 13px; }

  /* Back */
  .world-map {
    position: absolute; left: 10px; top: 20px; width: 580px; height: 310px;
    background: radial-gradient(ellipse at center, var(--map-grey) 0%, rgba(220,220,220,0.4) 55%, rgba(220,220,220,0) 75%);
  }
  .services {
    position: absolute; left: 0; right: 0; top: 79px; text-align: center;
    font-size: 14px; line-height: 19px; list-style: none;
  }
  .callout {
    position: absolute; left: 0; right: 0; top: 155px; text-align: center;
    font-size: 16.5px; font-weight: 900; line-height: 21px;
  }
  .availability {
    position: absolute; left: 0; right: 0; top: 216px; text-align: center;
    font-size: 19px; font-weight: 900;
    display: flex; justify-content: center; align-items: center; gap: 6px;
  }
  .availability svg { width: 18px; height: 18px; }
  .web-link {
    position: absolute; left: 0; right: 0; top: 245px; text-align: center;
    font-size: 17px; color: var(--brand-blue);
  }
  .web-link strong { font-weight: 900; }
</style>
</head>
<body>

<section class="card card-front" aria-label="Card front">
  <svg class="shapes" viewBox="0 0 600 341" width="600" height="341">
    <path d="M0,228 C60,312 180,300 300,212 S520,72 600,86 L600,341 L0,341 Z" fill="var(--brand-blue)"/>
    <path d="M0,214 C60,298 180,288 300,200 S520,60 600,74" fill="none" stroke="var(--brand-blue)" stroke-width="4"/>
  </svg>

  <div class="brand-mark" aria-hidden="true"></div>
  <div class="brand-name">Corvana<br>Tongue Works<br>LLC</div>

  <div class="person">
    <div class="person-name">RHODA PELLING</div>
    <div class="person-title">PRESIDENT</div>
  </div>

  <ul class="contact-list">
    <li>482 Garnet Ave., Ste. 219
      <svg viewBox="0 0 24 24"><path d="M12 2a7 7 0 0 0-7 7c0 5 7 13 7 13s7-8 7-13a7 7 0 0 0-7-7zm0 10a3 3 0 1 1 0-6 3 3 0 0 1 0 6z" fill="var(--ink)"/></svg></li>
    <li>Indianapolis, IN 40917, USA<span class="spacer"></span></li>
    <li class="gap">(555) 481-3062
      <svg viewBox="0 0 24 24"><path d="M6.6 10.8a15 15 0 0 0 6.6 6.6l2.2-2.2a1 1 0 0 1 1-.25 11 11 0 0 0 3.6.6 1 1 0 0 1 1 1V20a1 1 0 0 1-1 1A17 17 0 0 1 3 4a1 1 0 0 1 1-1h3.5a1 1 0 0 1 1 1c0 1.25.2 2.45.6 3.6a1 1 0 0 1-.25 1z" fill="var(--ink)"/></svg></li>
    <li>rmpelling@corvanatongueworks.example
      <svg viewBox="0 0 24 24"><path d="M2 5h20v14H2z" fill="var(--ink)"/><path d="M2 5l10 8 10-8" fill="none" stroke="var(--card-white)" stroke-width="2"/></svg></li>
    <li>www.corvanatongue.example
      <svg viewBox="0 0 24 24"><circle cx="12" cy="12" r="10" fill="var(--ink)"/><path d="M2 12h20M12 2c-4 4-4 16 0 20M12 2c4 4 4 16 0 20" fill="none" stroke="var(--card-white)" stroke-width="1.5"/></svg></li>
  </ul>
</section>

<section class="card card-back" aria-label="Card back">
  <div class="world-map" role="img" aria-label="Faint dotted world map in light grey"></div>

  <ul class="services">
    <li>ESL / ENL Language Classes, Private Lessons, &amp; Online Tutors</li>
    <li>PLEXA Training &amp; Testing</li>
    <li>Translating &amp; Interpreting Services</li>
  </ul>

  <p class="callout">CONTACT US ABOUT OVER-THE-PHONE<br>INTERPRETING IN OVER 200 LANGUAGES</p>

  <p class="availability">
    <svg viewBox="0 0 24 24"><circle cx="12" cy="12" r="10" fill="none" stroke="var(--ink)" stroke-width="2"/><path d="M12 12V6M12 12l-4 5" stroke="var(--ink)" stroke-width="2" fill="none"/></svg>
    24/7/365
  </p>

  <p class="web-link">www.<strong>CORVANATONGUE</strong>.example</p>
</section>

</body>
</html>
```